Help design website for "Brightwater Civic Advisors" to advance the common good

Here is the Google doc link that lays out the design:

https://files.plumrivet.example/sheet/d/7QmTzR2wLx9KpVbN4hJcY8sEaUoFdG3iXkMnPq5rWt6/edit?usp=sharing

Here is the Google drive folder with the logos and photos: https://vault.plumrivet.example/open?id=4HkWp9LzQe2TxRvN8mBaYc3DsUoJfG6

The testimonials are being gathered and will be shared by Friday, 1/4.

The winner will also have to migrate the coding files to my hosting site.

Thank you for your help! Looking forward to seeing your designs.

Target Market(s)

Prospective clients

Industry/Entity Type

Non Profit

Coding

Coded - Design and coding required

Number of Pages Required

5+ page

Requirements
Must have
• Noted in the Google doc regarding layout.
Nice to have

```html
<!DOCTYPE html>
<html lang="en">
<head>
<meta charset="utf-8">
<title>Brightwater Civic Advisors</title>
<link rel="stylesheet" href="https://fonts.googleapis.com/css2?family=Montserrat:wght@400;500;600;700&family=Open+Sans:ital,wght@0,400;0,600;1,400&display=swap">
<style>
:root{
  --blue:#3a86c8;
  --blue-dark:#2d6fa9;
  --ink:#1c1c1c;
  --text:#444;
  --muted:#8a8a8a;
  --grey-box:#f1f1f1;
  --grey-panel:#4a4a4a;
  --line:#d9d9d9;
  --footer:#141414;
  --white:#fff;
}
*{margin:0;padding:0;box-sizing:border-box}
html,body{width:1200px;height:4196px;overflow:hidden}
body{position:relative;background:var(--white);font-family:"Open Sans",Arial,sans-serif;color:var(--text)}
.abs{position:absolute}
h1,h2,h3,.nav a,.btn{font-family:"Montserrat",Arial,sans-serif}

/* header */
.site-header{left:0;top:0;width:1200px;height:112px;background:var(--white)}
.nav{left:112px;top:40px;display:flex;gap:26px}
.nav a{font-size:15px;font-weight:600;color:var(--ink);text-decoration:none;text-transform:uppercase;position:relative}
.nav a.active::before{content:"";position:absolute;left:0;right:0;top:-40px;height:4px;background:var(--blue)}
.brand{left:770px;top:30px;display:flex;align-items:center;gap:14px}
.brand-mark{width:40px;height:40px;background:var(--blue)}
.brand-name{font-family:"Montserrat",Arial,sans-serif;font-weight:600;font-size:22px;letter-spacing:3px;color:var(--blue-dark);text-transform:uppercase;line-height:1.1}

/* hero */
.hero{left:0;top:112px;width:1200px;height:590px;background:linear-gradient(135deg,#3a2420 0%,#6b3f2e 35%,#4a2c25 65%,#2a1b18 100%)}
.hero-shade{left:0;top:0;width:1200px;height:590px;background:rgba(0,0,0,.25)}
.hero-title{left:0;top:175px;width:1200px;text-align:center;color:var(--white);font-size:78px;font-weight:700;line-height:80px;text-transform:uppercase;letter-spacing:1px}
.hero-tag{left:0;top:335px;width:1200px;text-align:center;color:var(--white);font-family:"Montserrat",Arial,sans-serif;font-size:22px;letter-spacing:8px}
.hero-cut{left:0;top:548px}

/* about */
.about-title{left:160px;top:730px;font-size:38px;font-weight:500;color:var(--ink)}
.about-box{left:160px;top:811px;width:553px;height:364px;background:var(--grey-box)}
.about-text{left:210px;top:840px;width:400px;font-size:13.5px;line-height:22px;color:var(--text)}
.about-text p{margin-bottom:14px}
.about-photo{left:640px;top:741px;width:372px;height:364px;background:linear-gradient(160deg,#d8d4cf,#6e5a4c 60%,#2a211d);box-shadow:0 6px 20px rgba(0,0,0,.25)}
.btn{display:flex;align-items:center;justify-content:center;background:var(--blue);color:var(--white);font-weight:600;font-size:14px;text-transform:uppercase;clip-path:polygon(8% 0,100% 0,92% 100%,0 100%)}
.about-btn{left:210px;top:1103px;width:137px;height:36px}

/* services */
.services{left:0;top:1303px;width:1200px;height:702px;display:grid;grid-template-columns:repeat(3,400px);grid-template-rows:repeat(2,351px)}
.service{position:relative;display:flex;align-items:flex-end;padding:0 38px 30px}
.service h3{color:var(--white);font-size:21px;font-weight:600;line-height:27px;text-shadow:0 1px 4px rgba(0,0,0,.5)}
.service.photo-a{background:linear-gradient(160deg,#5d4a49,#2e2624)}
.service.photo-b{background:linear-gradient(160deg,#7b6a5a,#3b3028)}
.service.photo-c{background:linear-gradient(160deg,#8aa0b8,#3e4c5a 70%)}
.service.photo-d{background:linear-gradient(160deg,#7a5a3c,#3a2a1e)}
.service.photo-e{background:linear-gradient(160deg,#3c4a5e,#a9b6c6)}
.service.feature{background:var(--blue);align-items:flex-start;flex-direction:column;padding:38px 40px}
.service.feature h3{text-shadow:none;margin-bottom:18px}
.service.feature p{color:var(--white);font-size:13px;line-height:22px;text-align:justify}

/* testimonials */
.map-fade{left:230px;top:2040px;width:760px;height:440px;border-radius:50%;background:radial-gradient(ellipse,#f3f4f6 0%,#fafafa 55%,rgba(255,255,255,0) 75%)}
.section-title{left:0;width:1200px;text-align:center;font-size:38px;font-weight:500;color:var(--ink)}
.quote-mark{left:160px;top:2200px}
.quote-text{left:190px;top:2198px;width:820px;font-size:13.5px;line-height:30px}
.avatar{left:160px;top:2310px;width:100px;height:100px;border-radius:50%;background:linear-gradient(150deg,#c9b8ac,#3b2b24)}
.reviewer{left:280px;top:2322px;font-size:13px;line-height:26px}
.reviewer em{font-style:italic}
.reviewer .link{color:var(--blue)}
.reviews-btn{left:830px;top:2341px;width:177px;height:37px;font-size:12px}

/* media */
.tile{position:absolute}
.ph-1{left:112px;top:2579px;width:277px;height:358px;background:linear-gradient(170deg,#cfd3d6,#5b5048 70%,#2e2925)}
.ph-2{left:808px;top:2579px;width:280px;height:288px;background:linear-gradient(170deg,#6c5e52,#3b302a)}
.ph-3{left:112px;top:2945px;width:277px;height:244px;background:linear-gradient(170deg,#6a6a5a,#3d3a32)}
.ph-4{left:394px;top:2875px;width:322px;height:314px;background:linear-gradient(170deg,#2a2422,#6e5d55 60%,#1d1a18)}
.ph-5{left:112px;top:3203px;width:478px;height:294px;background:linear-gradient(180deg,#c8cfd6,#7c8a74 55%,#3f4a36)}
.ph-6{left:599px;top:3203px;width:489px;height:294px;background:linear-gradient(180deg,#a4a89a,#5b5e4e 60%,#35372c)}
.tile-caption{position:absolute;left:26px;bottom:18px;color:var(--white);font-family:"Montserrat",Arial,sans-serif;font-weight:600;font-size:20px;text-shadow:0 1px 4px rgba(0,0,0,.5)}
.articles{left:394px;top:2579px;width:406px;height:288px;background:var(--blue);padding:44px 30px;color:var(--white)}
.articles h3,.mlk h3{font-size:21px;font-weight:600;margin-bottom:16px}
.articles p,.mlk p{font-size:12.5px;line-height:24px;margin-bottom:6px}
.articles u,.mlk u{text-decoration:underline}
.view-all{font-size:10.5px;text-decoration:underline;margin-top:10px;display:block}
.mlk{left:724px;top:2875px;width:364px;height:314px;background:var(--grey-panel);padding:24px 30px;color:var(--white)}
.mlk h3{line-height:28px}
.player{position:absolute;left:0;right:0;bottom:0;height:34px;display:flex;align-items:center;padding:0 12px;gap:12px}
.player .track{flex:1;height:3px;background:rgba(255,255,255,.7)}
.play{position:absolute;left:50%;top:50%;width:58px;height:40px;margin:-20px 0 0 -29px;border-radius:10px;background:#222}

/* contact */
.contact-title{left:160px;top:3628px;font-size:38px;font-weight:500;color:var(--ink)}
.contact-brand{left:160px;top:3722px}
.contact-brand .brand-name{font-size:17px;letter-spacing:2px}
.contact-brand .brand-mark{width:32px;height:32px}
.field{position:absolute;left:500px;width:535px;height:45px;border:1px solid var(--line);font-size:13px;color:#777;padding:12px 16px}
.submit{left:492px;top:3924px;width:188px;height:43px}

/* footer */
.site-footer{left:0;top:4064px;width:1200px;height:132px;background:var(--footer)}
.copyright{left:112px;top:4118px;color:#ddd;font-size:12.5px}
.social{top:4121px;width:14px;height:14px;border-radius:50%;background:#fff}
</style>
</head>
<body>

<header class="abs site-header">
  <nav class="abs nav">
    <a class="active">Home</a><a>About Us</a><a>Services &amp; Testimonials</a><a>Media &amp; Impact</a><a>Contact</a>
  </nav>
  <div class="abs brand"><span class="brand-mark"></span><span class="brand-name">Brightwater<br>Civic Advisors</span></div>
</header>

<section class="abs hero" role="img" aria-label="Workshop participants talking at tables in a warm-lit hall">
  <div class="abs hero-shade"></div>
  <h1 class="abs hero-title">Brightwater<br>Civic Advisors</h1>
  <div class="abs hero-tag">Advancing The Common Good</div>
  <svg class="abs" style="left:588px;top:398px" width="24" height="34" viewBox="0 0 24 34"><rect x="5" y="1" width="14" height="22" rx="7" fill="none" stroke="#fff" stroke-width="2"/><line x1="12" y1="6" x2="12" y2="11" stroke="#fff" stroke-width="2"/><line x1="12" y1="24" x2="12" y2="32" stroke="#fff" stroke-width="2"/></svg>
  <svg class="abs hero-cut" width="1200" height="42" viewBox="0 0 1200 42" preserveAspectRatio="none" style="top:448px;height:142px"><polygon points="0,142 600,0 1200,142" fill="#fff"/><polyline points="0,138 600,0 1200,138" fill="none" stroke="#3a86c8" stroke-width="6"/></svg>
</section>

<h2 class="abs about-title">About Me</h2>
<div class="abs about-box"></div>
<div class="abs about-text">
  <p>Brightwater Civic Advisors supports nonprofit organizations and educational institutions to carry out their missions to benefit the wider community</p>
  <p>Founder Dana Whitfield is an educator with a 22-year record of demonstrated achievement and leadership roles in nonprofits and educational institutions. Most recently, she served as Associate Dean of Students in the University and Director of the University Community Service Center at Lakeshore University.</p>
</div>
<div class="abs about-photo" role="img" aria-label="Portrait of the founder"></div>
<div class="abs btn about-btn">Read More</div>

<section class="abs services">
  <div class="service photo-a" role="img" aria-label="Staff group photo at a training event"><h3>Staff Professional<br>Development</h3></div>
  <div class="service feature"><h3>Community Partnership<br>Development</h3><p>Dana has collaborated with more than 250 nonprofits, schools, government agencies, and businesses with corporate social responsibility units to create mutually beneficial partnerships. These relationships have been strengthened and sustained to expand programming and initiatives that meet community engagement outcomes.</p></div>
  <div class="service photo-b" role="img" aria-label="Group gathered in a gallery space"><h3>Group Facilitation &amp; Leadership<br>Training</h3></div>
  <div class="service photo-c" role="img" aria-label="Large group celebrating by the lake"><h3>Program Design, Implementation,<br>&amp; Evaluation</h3></div>
  <div class="service photo-d" role="img" aria-label="Speakers at a podium in a wood-panelled hall"><h3>Event Planning</h3></div>
  <div class="service photo-e" role="img" aria-label="Presenter beside a projected slide"><h3>Strategic Planning &amp; Visioning</h3></div>
</section>

<div class="abs map-fade" role="img" aria-label="Faint world map backdrop"></div>
<h2 class="abs section-title" style="top:2118px">Testimonials</h2>
<svg class="abs quote-mark" width="22" height="16" viewBox="0 0 22 16" style="top:2207px"><path d="M2 15 Q1 6 8 2 L9 4 Q5 7 6 9 L9 9 L9 15Z M13 15 Q12 6 19 2 L20 4 Q16 7 17 9 L20 9 L20 15Z" fill="none" stroke="#333" stroke-width="1.3"/></svg>
<p class="abs quote-text">Lorem ipsum dolor sit amet, consectetur adipiscing elit, sed do eiusmod tempor incididunt ut labore et dolore magna aliqua. Ut enim ad minim veniam, quis nostrud exercitation ullamco laboris nisi ut aliquip ex ea commodo consequat. Duis aute irure dolor in reprehenderit in voluptate velit esse cillum dolore eu fugiat nulla pariatur</p>
<div class="abs avatar" role="img" aria-label="Reviewer portrait"></div>
<div class="abs reviewer">Evan Marlow, Chief Operations &amp; Growth Officer, Open Horizons<br><em>2 June</em><br><span class="link">Sed ut perspiciatis unde</span></div>
<div class="abs btn reviews-btn">See More Reviews</div>

<h2 class="abs section-title" style="top:2496px">Media &amp; Impact</h2>
<div class="tile ph-1" role="img" aria-label="Musicians performing outdoors"><span class="tile-caption">April 2018</span></div>
<div class="abs articles">
  <h3>Articles</h3>
  <p>Attendees listening to a speaker at the Bright Path Dinner Dialogue event <u>(featured in March 2018 article)</u></p>
  <p>Students performing at the third annual Riverside Park Arts Festival <u>(featured in April 2018 article)</u></p>
  <span class="view-all">VIEW ALL</span>
</div>
<div class="tile ph-2" role="img" aria-label="Dinner guests seated at round tables"><span class="tile-caption">March 2018</span></div>
<div class="tile ph-3" role="img" aria-label="Video still of a speaker">
  <div class="player"><svg width="14" height="14" viewBox="0 0 14 14"><path d="M1 5h3l4-3v10l-4-3H1z" fill="#fff"/></svg><span class="track"></span><svg width="12" height="14" viewBox="0 0 12 14"><path d="M1 1v12M1 13h10" stroke="#fff" stroke-width="2"/></svg></div>
</div>
<div class="tile ph-4" role="img" aria-label="Video still of a speaker at a podium">
  <div class="player"><svg width="14" height="14" viewBox="0 0 14 14"><path d="M1 5h3l4-3v10l-4-3H1z" fill="#fff"/></svg><span class="track"></span><svg width="12" height="14" viewBox="0 0 12 14"><path d="M1 1v12M1 13h10" stroke="#fff" stroke-width="2"/></svg></div>
</div>
<div class="abs mlk">
  <h3>Dana welcoming volunteers for the annual Unity Day of Service</h3>
  <p>"Dreams, Ideas, and You" – A conversation with Dana Whitfield on how to get involved in the Northgate/Elmwood community <u>(February 2018)</u></p>
  <span class="view-all">VIEW ALL</span>
</div>
<div class="tile ph-5" role="img" aria-label="Video still of a group touring a city plaza">
  <svg class="play" viewBox="0 0 58 40"><rect width="58" height="40" rx="10" fill="#222"/><polygon points="23,12 38,20 23,28" fill="#fff"/></svg>
</div>
<div class="tile ph-6" role="img" aria-label="Video still of volunteers gathered outdoors">
  <svg class="play" viewBox="0 0 58 40"><rect width="58" height="40" rx="10" fill="#222"/><polygon points="23,12 38,20 23,28" fill="#fff"/></svg>
</div>

<h2 class="abs contact-title">Contact Us</h2>
<div class="abs brand contact-brand"><span class="brand-mark"></span><span class="brand-name">Brightwater<br>Civic Advisors</span></div>
<div class="field" style="top:3630px">Name</div>
<div class="field" style="top:3688px">Email</div>
<div class="field" style="top:3744px">Subject</div>
<div class="field" style="top:3800px;height:90px">Message</div>
<div class="abs btn submit">Submit</div>

<footer class="abs site-footer"></footer>
<div class="abs copyright">2019 Copyrights.All Rights Reserved</div>
<span class="abs social" style="left:1028px"></span>
<span class="abs social" style="left:1070px"></span>

</body>
</html>
```